Design and Renovation Company Luxury Business Card

I want to create a luxury business card for a Design and Renovation Firm . We will use our current logo. The company name is 528BUILDA. We do not want anything standard. We need a very unique concept.
Please see uploaded inspiration. I really like the textured paper option. I would like the card to be thick with debossing, and/or embossing options. The logo has orange in it but I would like to see the card with and without the orange. I think the orange may make the company feel less high-end. The goal is to elevate the logo not match its vibe per se of the logo. We want something very unique, not standard at all!
I would like a space for :
Logo,
Name,
Position,
Email,
Office number,
Website Address,
Business Address,
Thank you!
Have fun!
Target Market(s)
Home owners Age 35 +
Industry/Entity Type
Design and Renovation
Contact Information for Business Card
Logo, Name, Position, Email, Office number, Website Address, Business Address,.
Colors
Designer to choose colors to be used in the design.
Requirements
Must have
- A luxury designer feel. Must be black or dark grey but open to other luxury ideas.
Nice to have
- Gold, silver, black embossing or debossing. Textured paper design.
Should not have
- A cheap look and feel.

```html
<!DOCTYPE html>
<html lang="en">
<head>
<meta charset="UTF-8">
<title>528BUILDA Business Card</title>
<link href="https://fonts.googleapis.com/css2?family=Roboto:wght@400;500;700&display=swap" rel="stylesheet">
<style>
  :root {
    --backdrop: #e2e2e2;
    --charcoal: #313131;
    --orange: #e4891d;
    --orange-bright: #ee8f1f;
    --white: #f4f4f4;
  }
  * { box-sizing: border-box; margin: 0; padding: 0; }
  html, body {
    width: 1200px;
    height: 1040px;
    overflow: hidden;
    background: var(--backdrop);
    font-family: "Roboto", Arial, sans-serif;
  }
  .canvas { position: relative; width: 1200px; height: 1040px; }
  .card {
    position: absolute;
    width: 644px;
    height: 366px;
    border-radius: 18px;
  }
  .card-front { left: 285px; top: 130px; background: var(--charcoal); color: var(--white); }
  .card-back { left: 285px; top: 567px; background: var(--orange); color: var(--white); }

  /* front */
  .brand-front {
    position: absolute; left: 96px; top: 104px; width: 168px; height: 156px;
    display: flex; align-items: center; justify-content: flex-end;
  }
  .brand-front .brand-name {
    font-size: 24px; font-weight: 500; letter-spacing: 1.5px; white-space: nowrap;
  }
  .divider {
    position: absolute; left: 291px; top: 104px;
    width: 1.5px; height: 156px; background: var(--white);
  }
  .details { position: absolute; left: 320px; top: 96px; }
  .person-name { font-size: 24px; font-weight: 700; color: var(--orange-bright); line-height: 1.1; }
  .person-role { font-size: 16px; line-height: 1.3; margin-left: 1px; }
  .address { margin-top: 10px; font-size: 15.5px; line-height: 20px; }
  .contacts { margin-top: 10px; list-style: none; font-size: 15.5px; line-height: 20px; }
  .contacts li { display: flex; align-items: center; gap: 8px; }
  .contacts svg { width: 14px; height: 14px; flex: none; }

  /* back */
  .brand-back {
    position: absolute; left: 0; right: 0; top: 140px;
    display: flex; flex-direction: column; align-items: center;
  }
  .brand-back .brand-name {
    font-size: 54px; font-weight: 500; letter-spacing: 4px; line-height: 54px;
  }
  .brand-back .tagline {
    margin-top: 4px;
    font-size: 14px; font-weight: 700; letter-spacing: 5px; white-space: nowrap;
  }
  .back-web {
    position: absolute; left: 0; right: 0; top: 306px;
    text-align: center; font-size: 15px; letter-spacing: 3.5px;
  }
</style>
</head>
<body>
<main class="canvas">
  <section class="card card-front">
    <div class="brand-front">
      <div class="brand-name">528BUILDA</div>
    </div>
    <div class="divider"></div>
    <div class="details">
      <h1 class="person-name">Aaron Whitlock</h1>
      <p class="person-role">President</p>
      <p class="address">4127 Harrow Lane<br>Linden Hill, NY 11402</p>
      <ul class="contacts">
        <li>
          <svg viewBox="0 0 24 24" aria-hidden="true"><path fill="#ee8f1f" d="M6.6 10.8a15.1 15.1 0 0 0 6.6 6.6l2.2-2.2c.3-.3.7-.4 1-.2 1.1.4 2.3.6 3.6.6.6 0 1 .4 1 1V20c0 .6-.4 1-1 1C10.6 21 3 13.4 3 4c0-.6.4-1 1-1h3.5c.6 0 1 .4 1 1 0 1.3.2 2.5.6 3.6.1.3 0 .7-.2 1z"/></svg>
          (555) 0142-7786
        </li>
        <li>
          <svg viewBox="0 0 24 24" aria-hidden="true"><rect x="2" y="5" width="20" height="14" fill="#ee8f1f"/><path d="M2 5l10 8 10-8" fill="none" stroke="#313131" stroke-width="1.8"/></svg>
          name@528BUILDA.com
        </li>
        <li>
          <svg viewBox="0 0 24 24" aria-hidden="true"><circle cx="12" cy="12" r="10" fill="#ee8f1f"/><path d="M7 7c2 1 2 3 4 3s1 3 3 4-1 4-2 6M15 4c-1 2 1 3 3 3" fill="none" stroke="#313131" stroke-width="1.6"/></svg>
          www.528BUILDA.com
        </li>
      </ul>
    </div>
  </section>

  <section class="card card-back">
    <div class="brand-back">
      <div class="brand-name">528BUILDA</div>
      <div class="tagline">Design and Renovation Firm</div>
    </div>
    <p class="back-web">www.528BUILDA.com</p>
  </section>
</main>
</body>
</html>
```